New PowerPoint Design Project

I need a company powerpoint template for my company, Varnok (see design file logo attached), that has a number of templated slides with an exciting supporting colour palette. Needs to have header and footer sections, tables in colour which support the logo colour, bar and line charts, dot point slides and image (placeholders) slides. Logo is attached.
The primary use of this template is to pitch for new work - ie about us page, previous clients page, then a breakdown of services offered in a table format with prices etc...
Updates

Hi everyone
Please see some example PPT templates that provide more of a guide as to what I need.

Thanks
Leopold

Font styles to use
Serif
Sans Serif

Colors
0054AA
0677BA
7BADD7
CADEEF
E8F1F8
00AB8E
00BBA5
67D7C9
C6EFE9
E9F9F6
59FF00
82FF00
B8FF75
E3FFCB
F4FFEA
FFC000
F8CF3A
FAE287
FDF2CF
FEFAEE

```html
<!DOCTYPE html>
<html lang="en">
<head>
<meta charset="utf-8">
<title>Varnok Presentation Template</title>
<link href="https://fonts.googleapis.com/css2?family=Cormorant+Garamond:wght@400;500&family=Libre+Baskerville:wght@700&family=Lato:wght@400;700&family=Montserrat:wght@600&display=swap" rel="stylesheet">
<style>
:root{
  --canvas:#031a17;
  --slide:#0a362f;
  --gold:#c98a2b;
  --amber:#ffc000;
  --yellow:#f8cf3a;
  --yellow-soft:#fae287;
  --teal:#00bba5;
  --teal-deep:#00ab8e;
  --teal-light:#67d7c9;
  --mint:#c6efe9;
  --blue:#0677ba;
  --blue-deep:#0054aa;
  --sky:#7badd7;
  --white:#ffffff;
  --ink:#0b0b0b;
  --line:#5c6b3a;
}
*{margin:0;padding:0;box-sizing:border-box}
html,body{width:1027px;height:1200px;overflow:hidden;background:var(--canvas)}
body{position:relative;font-family:'Lato',sans-serif;font-weight:400;color:var(--white)}
.slide{position:absolute;width:467px;height:263px;background:var(--slide);overflow:hidden}
.col-a{left:33px}.col-b{left:533px}
.row-1{top:23px}.row-2{top:317px}.row-3{top:610px}.row-4{top:907px}
.abs{position:absolute}
.photo{position:absolute;inset:0}
.brand{position:absolute;font-family:'Cormorant Garamond',serif;font-weight:400;color:var(--gold);line-height:1;white-space:nowrap}
.brand-corner{right:22px;top:16px;font-size:21px}
.heading{position:absolute;left:23px;top:9px;font-family:'Libre Baskerville',serif;font-weight:700;font-size:11px;color:var(--gold);white-space:nowrap}
.marker{position:absolute;display:flex;align-items:center;gap:3px}
.marker .dot{width:4.5px;height:4.5px;border-radius:50%;background:var(--gold)}
.marker .pill{width:18px;height:4px;border-radius:2px;background:linear-gradient(90deg,var(--yellow),rgba(248,207,58,.15))}
.heading-marker{left:23px;top:26px}
.footer{position:absolute;left:0;right:0;bottom:0;height:18px;border-radius:18px 18px 0 0;background:linear-gradient(90deg,var(--gold) 0%,#d9a83a 45%,#f0e05a 100%);color:var(--ink)}
.footer .date{position:absolute;left:23px;top:6px;font-family:'Montserrat',sans-serif;font-weight:600;font-size:4.6px}
.footer .copy{position:absolute;left:0;right:0;top:5.5px;text-align:center;font-family:'Libre Baskerville',serif;font-weight:700;font-size:5px}
.footer .page{position:absolute;right:23px;top:3px;width:12px;height:12px;border-radius:50%;background:var(--ink);color:var(--white);font-family:'Montserrat',sans-serif;font-weight:600;font-size:4.6px;display:flex;align-items:center;justify-content:center}
/* cover */
.cover-brand{left:0;right:0;top:9px;text-align:center;font-size:25px}
.cover-title{left:0;right:0;top:46px;text-align:center;font-family:'Libre Baskerville',serif;font-weight:700;font-size:14.5px;color:var(--white);white-space:nowrap}
.cover-sub{left:0;right:0;top:71px;text-align:center;font-family:'Libre Baskerville',serif;font-weight:700;font-size:7.3px;color:var(--yellow)}
/* toc */
.toc-item{position:absolute;width:200px;height:34px}
.toc-num{position:absolute;left:0;top:6px;width:14px;text-align:center;font-family:'Libre Baskerville',serif;font-size:12px;color:var(--gold)}
.toc-rule{position:absolute;left:22px;top:0;width:1px;height:30px;background:rgba(201,138,43,.5)}
.toc-title{position:absolute;left:30px;top:-3px;font-family:'Libre Baskerville',serif;font-weight:700;font-size:8.5px;color:var(--gold);white-space:nowrap}
.toc-text{position:absolute;left:30px;top:10px;width:145px;font-size:5.3px;line-height:9.8px}
/* intro */
.intro-title{left:0;right:0;top:104px;text-align:center;font-family:'Libre Baskerville',serif;font-weight:700;font-size:24px;background:linear-gradient(90deg,var(--gold),var(--yellow));-webkit-background-clip:text;background-clip:text;-webkit-text-fill-color:transparent}
/* about */
.para{position:absolute;text-align:center;font-weight:400;font-size:7.3px;line-height:14px}
.stat{position:absolute;width:100px;text-align:center;top:163px}
.stat-num{font-size:16px;line-height:20px}
.stat-dash{width:4px;height:1.5px;background:var(--yellow);margin:1px auto 5px}
.stat-label{font-size:7.2px}
/* clients */
.card{position:absolute;top:92px;width:110px}
.card-img{position:relative;height:83px}
.card-title{margin-top:9px;text-align:center;font-weight:700;font-size:7.2px}
.card-text{margin-top:4px;text-align:center;font-size:5.8px;line-height:8.8px}
/* graph */
.g-num{position:absolute;left:20px;width:60px;text-align:center;font-size:17px;color:var(--yellow)}
.g-label{position:absolute;font-size:7.2px;color:var(--yellow)}
.bar{position:absolute;bottom:90px;width:20px;background:var(--gold)}
.bar.peak{background:var(--yellow)}
.bar-label{position:absolute;top:178px;width:20px;text-align:center;font-size:5.5px;color:var(--gold)}
.trend{position:absolute;left:0;top:0}
.g-side{position:absolute;left:357px;top:72px;width:90px;font-size:6.8px;line-height:12.2px;text-align:justify}
.g-note{position:absolute;left:119px;top:197px;width:215px;font-size:7.2px;line-height:14.5px}
/* services table */
.grid{position:absolute;left:24px;top:66px;width:420px;border-collapse:collapse;table-layout:fixed}
.grid th{background:var(--gold);height:25px;font-weight:700;font-size:7px;color:var(--white);border-right:1px solid rgba(255,255,255,.25)}
.grid td{height:23px;text-align:center;border:1px solid var(--line)}
.grid svg{display:inline-block;vertical-align:middle}
.grid .price td{background:var(--teal-deep);color:var(--white);font-weight:700;font-size:7px;border-color:var(--teal)}
/* contact */
.contact-brand{left:0;right:0;top:62px;text-align:center;font-size:25px}
.contact-info{position:absolute;top:145px;display:flex;align-items:center;gap:5px}
.contact-icon{width:18px;height:18px;border-radius:50%;background:var(--gold);display:flex;align-items:center;justify-content:center}
.contact-label{font-family:'Montserrat',sans-serif;font-weight:600;font-size:5.8px;color:var(--yellow)}
.contact-value{font-weight:700;font-size:7.3px;margin-top:2px}
.thanks{left:0;right:0;top:189px;text-align:center;font-family:'Libre Baskerville',serif;font-weight:700;font-size:12px;color:var(--yellow)}
</style>
</head>
<body>

<section class="slide col-a row-1">
  <div class="photo" role="img" aria-label="Sports car photographed in a dark studio with amber and teal light" style="background:radial-gradient(ellipse at 30% 70%,#7fb5a6 0%,#2f5a52 25%,transparent 55%),radial-gradient(ellipse at 85% 45%,#5a3a10 0%,transparent 60%),linear-gradient(180deg,#0d3a33 0%,#2a2a12 45%,#1a1a0c 100%)"></div>
  <div class="brand cover-brand">VARNOK</div>
  <div class="abs cover-title">ELEVATE YOUR VISION WITH VARNOK</div>
  <div class="abs cover-sub">Creative strategy and delivery for ambitious brands.</div>
  <div class="footer"><span class="date">12 April 2025</span><span class="copy">Copyrights@2025.Varnok.All Rights Reserved</span><span class="page">01</span></div>
</section>

<section class="slide col-b row-1">
  <h2 class="heading">TABLE OF CONTENT</h2>
  <div class="marker heading-marker"><span class="dot"></span><span class="pill"></span></div>
  <div class="brand brand-corner">VARNOK</div>
  <div class="toc-item" style="left:30px;top:59px"><span class="toc-num">1</span><span class="toc-rule"></span><span class="toc-title">About Varnok</span><p class="toc-text">Itaque earum rerum hic tenetur a sapiente delectus, ut aut reiciendis voluptatibus</p></div>
  <div class="toc-item" style="left:247px;top:59px"><span class="toc-num">2</span><span class="toc-rule"></span><span class="toc-title">Introduction</span><p class="toc-text">Itaque earum rerum hic tenetur a sapiente delectus, ut aut reiciendis voluptatibus</p></div>
  <div class="toc-item" style="left:30px;top:125px"><span class="toc-num">3</span><span class="toc-rule"></span><span class="toc-title">Previous Clients</span><p class="toc-text">Itaque earum rerum hic tenetur a sapiente delectus, ut aut reiciendis voluptatibus</p></div>
  <div class="toc-item" style="left:247px;top:125px"><span class="toc-num">4</span><span class="toc-rule"></span><span class="toc-title">Our Services</span><p class="toc-text">Itaque earum rerum hic tenetur a sapiente delectus, ut aut reiciendis voluptatibus</p></div>
  <div class="toc-item" style="left:30px;top:191px"><span class="toc-num">5</span><span class="toc-rule"></span><span class="toc-title">Our Graph</span><p class="toc-text">Itaque earum rerum hic tenetur a sapiente delectus, ut aut reiciendis voluptatibus</p></div>
  <div class="toc-item" style="left:247px;top:191px"><span class="toc-num">6</span><span class="toc-rule"></span><span class="toc-title">Contact Us</span><p class="toc-text">Itaque earum rerum hic tenetur a sapiente delectus, ut aut reiciendis voluptatibus</p></div>
  <div class="footer"><span class="date">12 April 2025</span><span class="copy">Copyrights@2025.Varnok.All Rights Reserved</span><span class="page">02</span></div>
</section>

<section class="slide col-a row-2">
  <div class="photo" role="img" aria-label="Classic car parked on a dim cobbled street at dusk" style="background:radial-gradient(ellipse at 55% 60%,#1f3a30 0%,transparent 60%),linear-gradient(180deg,#15241e 0%,#0f1c17 55%,#0a1410 100%)"></div>
  <div class="brand brand-corner">VARNOK</div>
  <div class="abs intro-title">INTRODUCTION</div>
  <div class="marker" style="left:222px;top:145px"><span class="dot"></span><span class="pill"></span></div>
  <div class="footer"><span class="date">12 April 2025</span><span class="copy">Copyrights@2025.Varnok.All Rights Reserved</span><span class="page">03</span></div>
</section>

<section class="slide col-b row-2">
  <h2 class="heading">ABOUT VARNOK</h2>
  <div class="marker heading-marker"><span class="dot"></span><span class="pill"></span></div>
  <div class="brand brand-corner">VARNOK</div>
  <p class="para" style="left:40px;right:40px;top:49px">Lorem ipsum dolor sit amet, consectetur adipiscing elit, sed do eiusmod tempor incididunt ut labore et dolore magna aliqua. Ut enim ad minim veniam, quis nostrud exercitation ullamco laboris nisi ut aliquip ex ea commodo consequat. Duis aute irure dolor in reprehenderit in voluptate velit esse cillum dolore eu fugiat nulla pariatur.</p>
  <p class="para" style="left:30px;right:30px;top:118px">Nemo enim ipsam voluptatem quia voluptas sit aspernatur aut odit aut fugit, sed quia consequuntur magni dolores eos qui ratione voluptatem sequi nesciunt.</p>
  <div class="stat" style="left:25px"><div class="stat-num">234</div><div class="stat-dash"></div><div class="stat-label">Excepteur sint</div></div>
  <div class="stat" style="left:126px"><div class="stat-num">123</div><div class="stat-dash"></div><div class="stat-label">Occaecat cupid</div></div>
  <div class="stat" style="left:227px"><div class="stat-num">230</div><div class="stat-dash"></div><div class="stat-label">Occaecat cupid</div></div>
  <div class="stat" style="left:327px"><div class="stat-num">233</div><div class="stat-dash"></div><div class="stat-label">Occaecat cupid</div></div>
  <div class="footer"><span class="date">12 April 2025</span><span class="copy">Copyrights@2025.Varnok.All Rights Reserved</span><span class="page">04</span></div>
</section>

<section class="slide col-a row-3">
  <h2 class="heading">PREVIOUS CLIENTS</h2>
  <div class="marker heading-marker"><span class="dot"></span><span class="pill"></span></div>
  <div class="brand brand-corner">VARNOK</div>
  <p class="para" style="left:25px;right:25px;top:53px;font-size:6.3px;line-height:11.5px">Lorem ipsum dolor sit amet, consectetur adipiscing elit, sed do eiusmod tempor incididunt ut labore et dolore magna aliqua. Ut enim ad minim veniam, quis nostrud exercitation ullamco laboris nisi ut aliquip ex ea commodo consequat.</p>
  <div class="card" style="left:23px"><div class="card-img" role="img" aria-label="Client project image: person charging a white electric car" style="background:linear-gradient(135deg,#c9d4d8 0%,#8a9a7e 45%,#e6ecee 100%)"></div><div class="card-title">Lorem ipsum dolor</div><p class="card-text">Excepteur sint occaecat cupidatat non proident, sunt in culpa qui officia deserunt mollit .</p></div>
  <div class="card" style="left:169px"><div class="card-img" role="img" aria-label="Client project image: white SUV on a country road" style="background:linear-gradient(180deg,#b9c6cc 0%,#7f8b6a 45%,#5b5e58 100%)"></div><div class="card-title">Lorem ipsum dolor</div><p class="card-text">Excepteur sint occaecat cupidatat non proident, sunt in culpa qui officia deserunt mollit .</p></div>
  <div class="card" style="left:315px"><div class="card-img" role="img" aria-label="Client project image: silver car by the sea at sunset" style="background:radial-gradient(ellipse at 20% 25%,#f4f1e6 0%,#9fb0b8 35%,#3d4548 100%)"></div><div class="card-title">Lorem ipsum dolor</div><p class="card-text">Excepteur sint occaecat cupidatat non proident, sunt in culpa qui officia deserunt mollit .</p></div>
  <div class="footer"><span class="date">12 April 2025</span><span class="copy">Copyrights@2025.Varnok.All Rights Reserved</span><span class="page">05</span></div>
</section>

<section class="slide col-b row-3">
  <h2 class="heading">OUR GRAPH</h2>
  <div class="marker heading-marker"><span class="dot"></span><span class="pill"></span></div>
  <div class="brand brand-corner">VARNOK</div>
  <div class="g-num" style="top:84px">657</div>
  <div class="g-label" style="left:24px;top:109px">Excepteur sint</div>
  <div class="g-num" style="top:134px;color:var(--gold)">472</div>
  <div class="g-label" style="left:24px;top:159px">Duis aute iruret</div>
  <div class="bar" style="left:123px;height:53px"></div>
  <div class="bar" style="left:157px;height:71px"></div>
  <div class="bar" style="left:194px;height:31px"></div>
  <div class="bar" style="left:230px;height:36px"></div>
  <div class="bar" style="left:265px;height:72px"></div>
  <div class="bar peak" style="left:302px;height:98px"></div>
  <svg class="trend" width="467" height="263" viewBox="0 0 467 263" aria-label="Trend line">
    <polyline points="133,112 167,98 204,122 240,116 275,94 312,70" fill="none" stroke="#00bba5" stroke-width="1.4" stroke-linejoin="round"/>
    <g fill="#0a362f" stroke="#67d7c9" stroke-width="1.2">
      <circle cx="133" cy="112" r="2"/><circle cx="167" cy="98" r="2"/><circle cx="204" cy="122" r="2"/><circle cx="240" cy="116" r="2"/><circle cx="275" cy="94" r="2"/><circle cx="312" cy="70" r="2"/>
    </g>
  </svg>
  <span class="bar-label" style="left:123px">F1</span>
  <span class="bar-label" style="left:157px">F2</span>
  <span class="bar-label" style="left:194px">F3</span>
  <span class="bar-label" style="left:230px">F4</span>
  <span class="bar-label" style="left:265px">F5</span>
  <span class="bar-label" style="left:302px">F6</span>
  <p class="g-note">Excepteur sint occaecat cupidatat non proident, sunt in culpa qui officia deserunt mollit anim id est laborum.</p>
  <p class="g-side">Duis aute irure dolor in reprehenderit in voluptate velit esse cillum dolore eu fugiat nulla pariatur.<br><br>Excepteur sint occaecat cupidatat non proident, sunt in culpa qui officia deserunt mollit anim id est laborum.</p>
  <div class="footer"><span class="date">12 April 2025</span><span class="copy">Copyrights@2025.Varnok.All Rights Reserved</span><span class="page">06</span></div>
</section>

<section class="slide col-a row-4">
  <h2 class="heading">OUR SERVICES</h2>
  <div class="marker heading-marker"><span class="dot"></span><span class="pill"></span></div>
  <div class="brand brand-corner">VARNOK</div>
  <svg width="0" height="0" style="position:absolute">
    <defs>
      <symbol id="tick" viewBox="0 0 10 10"><path d="M1.5 5.2 4 7.6 8.6 2.4" fill="none" stroke="#f8cf3a" stroke-width="1.8" stroke-linecap="round" stroke-linejoin="round"/></symbol>
      <symbol id="cross" viewBox="0 0 10 10"><path d="M2.5 2.5 7.5 7.5M7.5 2.5 2.5 7.5" fill="none" stroke="#c98a2b" stroke-width="1.8" stroke-linecap="round"/></symbol>
    </defs>
  </svg>
  <table class="grid">
    <thead><tr><th>Itaque earum</th><th>Reiciendis vopbus</th><th>Occaecati cupidi</th><th>Similique sunt</th><th>Dignissimos ducim</th></tr></thead>
    <tbody>
      <tr><td><svg width="7" height="7"><use href="#tick"/></svg></td><td><svg width="7" height="7"><use href="#tick"/></svg></td><td><svg width="7" height="7"><use href="#tick"/></svg></td><td><svg width="7" height="7"><use href="#tick"/></svg></td><td><svg width="7" height="7"><use href="#tick"/></svg></td></tr>
      <tr><td><svg width="7" height="7"><use href="#tick"/></svg></td><td><svg width="7" height="7"><use href="#tick"/></svg></td><td><svg width="6" height="6"><use href="#cross"/></svg></td><td><svg width="7" height="7"><use href="#tick"/></svg></td><td><svg width="7" height="7"><use href="#tick"/></svg></td></tr>
      <tr><td><svg width="7" height="7"><use href="#tick"/></svg></td><td><svg width="7" height="7"><use href="#tick"/></svg></td><td><svg width="7" height="7"><use href="#tick"/></svg></td><td><svg width="7" height="7"><use href="#tick"/></svg></td><td><svg width="7" height="7"><use href="#tick"/></svg></td></tr>
      <tr><td><svg width="6" height="6"><use href="#cross"/></svg></td><td><svg width="7" height="7"><use href="#tick"/></svg></td><td><svg width="6" height="6"><use href="#cross"/></svg></td><td><svg width="7" height="7"><use href="#tick"/></svg></td><td><svg width="7" height="7"><use href="#tick"/></svg></td></tr>
      <tr><td><svg width="7" height="7"><use href="#tick"/></svg></td><td><svg width="7" height="7"><use href="#tick"/></svg></td><td><svg width="7" height="7"><use href="#tick"/></svg></td><td><svg width="7" height="7"><use href="#tick"/></svg></td><td><svg width="7" height="7"><use href="#tick"/></svg></td></tr>
      <tr class="price"><td>$1,200</td><td>$1,800</td><td>$2,400</td><td>$3,100</td><td>$4,500</td></tr>
    </tbody>
  </table>
  <div class="footer"><span class="date">12 April 2025</span><span class="copy">Copyrights@2025.Varnok.All Rights Reserved</span><span class="page">07</span></div>
</section>

<section class="slide col-b row-4">
  <h2 class="heading">CONTACT US</h2>
  <div class="marker heading-marker"><span class="dot"></span><span class="pill"></span></div>
  <div class="brand contact-brand">VARNOK</div>
  <p class="para" style="left:35px;right:35px;top:101px;font-size:6.3px;line-height:11.5px">Lorem ipsum dolor sit amet, consectetur adipiscing elit, sed do eiusmod tempor incididunt ut labore et dolore magna aliqua. Ut enim ad minim veniam, quis nostrud exercitation ullamco laboris nisi ut aliquip ex ea commodo consequat.</p>
  <div class="contact-info" style="left:70px">
    <span class="contact-icon"><svg width="8" height="9" viewBox="0 0 10 12"><path d="M5 0.8C2.8 0.8 1.2 2.5 1.2 4.6 1.2 7.4 5 11.2 5 11.2S8.8 7.4 8.8 4.6C8.8 2.5 7.2 0.8 5 0.8Z" fill="#0a362f"/><circle cx="5" cy="4.6" r="1.5" fill="#c98a2b"/></svg></span>
    <div><div class="contact-label">LOCATION:</div><div class="contact-value">Varnok, US</div></div>
  </div>
  <div class="contact-info" style="left:180px">
    <span class="contact-icon"><svg width="8" height="6" viewBox="0 0 10 7"><rect x="0.5" y="0.5" width="9" height="6" rx="0.8" fill="#0a362f"/><path d="M1 1 5 4 9 1" fill="none" stroke="#c98a2b" stroke-width="0.9"/></svg></span>
    <div><div class="contact-label">EMAIL US:</div><div class="contact-value">info@varnok.com</div></div>
  </div>
  <div class="contact-info" style="left:319px">
    <span class="contact-icon"><svg width="8" height="8" viewBox="0 0 10 10"><path d="M2.2 0.8 3.8 2.8 3 4C3.6 5.3 4.7 6.4 6 7L7.2 6.2 9.2 7.8 8.4 9.2C4.6 9.3 0.7 5.4 0.8 1.6Z" fill="#0a362f"/></svg></span>
    <div><div class="contact-label">PHONE NUMBER:</div><div class="contact-value">+1 555 010 0199</div></div>
  </div>
  <div class="abs thanks">THANK YOU</div>
  <div class="footer"><span class="date">12 April 2025</span><span class="copy">Copyrights@2025.Varnok.All Rights Reserved</span><span class="page">08</span></div>
</section>

</body>
</html>
```